Fire Risk Assessment App needs a sleek UI design

I need a sleek, modern but professional design for my 5 page Fire Risk Assessment App. Include gradient background, fire themed colours including reds, yellows, light orange and a touch of black. Design must ooze simplicity and professionalism. This is for the UK market. See attached images and word doc for more information.

Target Market(s)

General public and business owners

Industry/Entity Type

Technology / Fire Safety

Colors
00AB8E
00BBA5
67D7C9
C6EFE9
E9F9F6
59FF00
82FF00
B8FF75
E3FFCB
F4FFEA
FFC000
F8CF3A
FAE287
FDF2CF
FEFAEE
F0912C
F2A743
F7CA91
FBE8D2
FDF5EE
EE7325
F08F49
F5BC92
FAE3D3
FDF4ED
EB3D1F
EC4F4E
F09395
F8D3D4
FCEDEE

```html
<!DOCTYPE html>
<html lang="en">
<head>
<meta charset="utf-8">
<title>Fire Risk Assessment App – UI Screens</title>
<link href="https://fonts.googleapis.com/css2?family=Poppins:wght@400;500;600;700&display=swap" rel="stylesheet">
<style>
:root{
  --bg-dark:#2e0f0f;
  --bg-mid:#4a1815;
  --red:#EB3D1F;
  --red-deep:#c9261a;
  --red-soft:#EC4F4E;
  --orange:#EE7325;
  --orange-light:#F0912C;
  --amber:#FFC000;
  --green:#00AB8E;
  --green-bright:#2bbd4a;
  --pink-tint:#FCEDEE;
  --peach-tint:#FDF4ED;
  --white:#ffffff;
  --ink:#1d1d1d;
  --grey:#8a8a8a;
  --line:#e8e3e1;
}
*{box-sizing:border-box;margin:0;padding:0}
html,body{width:836px;height:1200px;overflow:hidden}
body{
  font-family:'Poppins',sans-serif;
  background:radial-gradient(ellipse at 50% 30%,var(--bg-mid),var(--bg-dark) 75%);
  position:relative;color:var(--white);
}
.screen{
  position:absolute;width:180px;height:440px;border-radius:24px;overflow:hidden;
  background:linear-gradient(180deg,var(--red) 0%,var(--red-deep) 100%);
  display:flex;flex-direction:column;
}
.screen--tall{height:680px}
.side-label{
  position:absolute;writing-mode:vertical-rl;transform:rotate(180deg);
  font-size:7px;letter-spacing:3.2px;color:var(--orange-light);font-weight:500;white-space:nowrap;
}
.status{display:flex;justify-content:space-between;align-items:center;padding:12px 16px 0;font-size:7px;font-weight:600}
.status svg{display:block}
.app-title{display:flex;align-items:center;gap:6px;padding:16px 12px 0;font-size:10px;font-weight:600}
.app-title .spacer{flex:1}
.sub{font-size:6px;padding:0 12px;margin-top:30px;font-weight:500}
.card{background:var(--white);color:var(--ink);border-radius:6px;margin:0 12px}
.row-head{display:flex;justify-content:space-between;font-size:6px;font-weight:600;padding:9px 8px 6px}
.link{color:var(--red);font-size:5px}
.item{display:flex;align-items:center;gap:7px;padding:7px 8px;border-radius:5px;background:var(--white);color:var(--ink)}
.item .ico{width:18px;height:18px;border-radius:50%;background:var(--pink-tint);display:flex;align-items:center;justify-content:center;flex:none}
.item .txt{flex:1;font-size:6px;font-weight:500;line-height:1.3}
.item .meta{font-size:4.5px;color:var(--grey);font-weight:400}
.chevron{color:var(--red);font-size:7px}
.tag{display:inline-block;font-size:4px;border-radius:6px;padding:1px 4px;font-weight:600;margin-top:2px}
.tag--progress{background:var(--peach-tint);color:var(--orange)}
.tag--done{background:#e4f7ef;color:var(--green)}
.dots{display:flex;justify-content:center;gap:2px;padding:4px 0}
.dots span{width:3px;height:2px;border-radius:2px;background:#ddd}
.dots span.on{width:12px;background:var(--red)}
.btn-orange{margin:6px 8px 9px;height:17px;border-radius:9px;background:linear-gradient(90deg,var(--orange),var(--red));color:var(--white);font-size:6px;font-weight:600;display:flex;align-items:center;justify-content:center;gap:5px}
.section-title{font-size:7.5px;font-weight:500;padding:18px 12px 6px}
.stack{display:flex;flex-direction:column;gap:3px;padding:0 12px}
.pill-outline{margin:9px auto 0;border:1px solid var(--white);border-radius:8px;font-size:5px;padding:2px 8px;font-weight:500}
.history{display:flex;gap:6px;padding:5px 12px;font-size:5.5px;font-weight:500;border-bottom:1px solid rgba(255,255,255,.15)}
.history .meta{font-size:4.5px;opacity:.8;font-weight:400}
.history .ico{width:13px;height:13px;border-radius:50%;background:var(--white);flex:none}
.tabbar{margin-top:auto;background:var(--white);display:flex;justify-content:space-around;padding:7px 6px 16px;color:var(--grey);font-size:3.8px;position:relative}
.tabbar div{display:flex;flex-direction:column;align-items:center;gap:2px}
.tabbar .active{color:var(--red);font-weight:600}
.tabbar::after,.home-bar::after{content:"";position:absolute;bottom:5px;left:50%;width:52px;height:2px;margin-left:-26px;border-radius:2px;background:var(--ink)}
.home-bar{position:relative;height:14px}
.home-bar--light::after{background:var(--white)}
.plan{margin:0 12px 8px;height:30px;border:1px solid var(--white);border-radius:5px;padding:0 7px;position:relative;display:flex;flex-direction:column;justify-content:center;align-items:flex-start;gap:1px}
.plan b{display:block;font-size:7px;font-weight:600;line-height:1.2}
.plan .level{display:inline-block;font-size:4.2px;line-height:1.5;background:var(--white);color:var(--red);border-radius:4px;padding:0 4px;font-weight:600}
.plan .flag{position:absolute;right:12px;top:-4px;font-size:3.8px;line-height:1.5;background:var(--white);color:var(--ink);border-radius:3px;padding:0 6px;font-weight:700}
.plan--chosen{background:var(--white);color:var(--red)}
.plan--chosen .level{background:var(--pink-tint);color:var(--ink)}
.plan--chosen .flag{background:var(--amber)}
.plan .check{position:absolute;right:7px;top:50%;margin-top:-4px;width:8px;height:8px;border-radius:50%;background:var(--red)}
.actions{display:flex;gap:8px;padding:0 12px}
.actions div{flex:1;height:18px;border-radius:9px;display:flex;align-items:center;justify-content:center;gap:5px;font-size:5.5px;font-weight:600}
.btn-ghost{border:1px solid var(--white);color:var(--white)}
.btn-solid{background:var(--white);color:var(--red)}
.btn-ghost-red{border:1px solid var(--red);color:var(--red)}
.btn-red{background:var(--red);color:var(--white)}
.choice{margin:0 12px 6px;height:26px;border-radius:13px;border:1px solid var(--white);display:flex;align-items:center;gap:6px;padding:0 4px;font-size:6px;font-weight:600}
.choice .ico{width:18px;height:18px;border-radius:50%;background:var(--white)}
.choice--chosen{background:var(--white);color:var(--red)}
.choice--chosen .ico{background:var(--pink-tint)}
.choice .check{margin-left:auto;margin-right:4px;width:8px;height:8px;border-radius:50%;background:var(--red)}
.flame-art{margin:6px auto 0;width:128px;height:128px;border-radius:50%;background:radial-gradient(circle,rgba(255,255,255,.22),rgba(255,255,255,.06))}
.q-head{padding:12px 12px 26px;position:relative}
.q-kicker{font-size:4.5px;font-weight:500}
.q-title{font-size:10px;font-weight:700;margin-top:2px}
.q-section{font-size:6px;margin-top:1px}
.q-section span{opacity:.8}
.save{position:absolute;right:10px;top:12px;display:flex;flex-direction:column;align-items:center;gap:2px;font-size:4.5px}
.save i{width:11px;height:11px;border-radius:50%;border:1px solid var(--white);display:block}
.q-body{flex:1;background:var(--white);color:var(--ink);border-radius:12px 12px 0 0;padding:0 12px;display:flex;flex-direction:column;position:relative}
.q-badge{width:30px;height:30px;border-radius:50%;background:var(--white);border:2px solid var(--green-bright);margin:-15px auto 0;display:flex;align-items:center;justify-content:center}
.q-topic{text-align:center;font-size:6px;font-weight:600;margin-top:6px}
.q-clause{text-align:center;font-size:5px;color:#555;padding-bottom:8px;border-bottom:1px solid var(--line)}
.q-num{font-size:4.5px;color:var(--red);font-weight:500;margin-top:8px}
.q-text{font-size:7px;font-weight:500;line-height:1.45;margin-top:5px}
.answers{display:flex;justify-content:space-around;margin-top:8px}
.answers div{display:flex;flex-direction:column;align-items:center;gap:3px;font-size:4.5px;font-weight:500}
.answers i{width:16px;height:16px;border-radius:50%;display:flex;align-items:center;justify-content:center;font-style:normal;font-size:8px;font-weight:700}
.a-no i{border:1px solid var(--red);color:var(--red)}
.a-na i{border:1px solid var(--orange-light);color:var(--orange-light)}
.a-yes i{border:1px solid var(--green-bright);color:var(--green-bright)}
.a-no.on i{background:var(--red);color:var(--white)}
.a-no.on{color:var(--red)}
.a-yes.on i{background:var(--green-bright);color:var(--white)}
.a-yes.on{color:var(--green-bright)}
.note{margin-top:8px;border:1px solid var(--line);border-radius:4px;font-size:4.5px;padding:5px 6px;font-weight:500}
.label-small{font-size:4.3px;color:var(--grey);margin-top:8px;font-weight:500}
.tools{display:flex;gap:4px;margin-top:4px}
.tools div{flex:1;background:var(--pink-tint);border-radius:4px;font-size:5px;padding:4px 6px;display:flex;align-items:center;gap:5px}
.photo{margin-top:5px;height:130px;border-radius:5px;background:linear-gradient(135deg,#6d6f72,#3a3c3f);position:relative}
.photo i{position:absolute;right:5px;top:5px;width:11px;height:11px;border-radius:50%;background:var(--white)}
.progress{margin-top:auto;padding-top:6px;border-top:1px solid var(--line)}
.progress .lbl{display:flex;justify-content:space-between;font-size:3.8px;font-weight:600}
.bar{height:2px;background:#e6e6e6;border-radius:2px;margin-top:4px}
.bar span{display:block;width:60%;height:100%;background:var(--green-bright);border-radius:2px}
.q-actions{padding:8px 0 0}
.q-actions.actions{padding-left:0;padding-right:0}
</style>
</head>
<body>

<div class="side-label" style="left:12px;top:90px;height:440px;text-align:center">DASHBOARD DESIGN ALT 1</div>
<div class="side-label" style="left:217px;top:90px;height:440px;text-align:center">PURCHASE OPTIONS</div>
<div class="side-label" style="left:422px;top:90px;height:440px;text-align:center">ADD NEW ASSESSMENT</div>
<div class="side-label" style="left:627px;top:90px;height:440px;text-align:center">ADD ASSESSMENT - QUESTION - ADD PHOTO</div>
<div class="side-label" style="left:12px;top:590px;height:440px;text-align:center">ADD ASSESSMENT - QUESTION - NONE</div>
<div class="side-label" style="left:217px;top:590px;height:440px;text-align:center">ADD ASSESSMENT - QUESTION - YES</div>
<div class="side-label" style="left:422px;top:590px;height:440px;text-align:center">ADD ASSESSMENT - QUESTION - NO</div>

<!-- Dashboard -->
<section class="screen" style="left:30px;top:90px">
  <div class="status"><span>9:41</span><svg width="22" height="6"><rect x="0" y="3" width="2" height="3" fill="#fff"/><rect x="3" y="2" width="2" height="4" fill="#fff"/><rect x="6" y="0" width="2" height="6" fill="#fff"/><rect x="12" y="1" width="9" height="4" rx="1" fill="#fff"/></svg></div>
  <div class="app-title"><svg width="11" height="11" viewBox="0 0 12 12"><circle cx="6" cy="6" r="5" fill="none" stroke="#fff" stroke-width="1.4"/><path d="M6 6l2-3" stroke="#fff" stroke-width="1.4"/></svg>Dashboard<span class="spacer"></span><svg width="11" height="11" viewBox="0 0 12 12"><circle cx="6" cy="6" r="5.5" fill="#fff"/><circle cx="6" cy="4.6" r="1.8" fill="#EB3D1F"/><path d="M2.8 9.5a3.4 3.4 0 0 1 6.4 0" fill="#EB3D1F"/></svg></div>
  <div class="card" style="margin-top:10px">
    <div class="row-head"><span>Fire Risk Assessments</span><span class="link">VIEW ALL</span></div>
    <div class="item" style="margin:0 4px;border:1px solid var(--line)"><div class="ico"><svg width="8" height="8"><rect x="1" y="1" width="6" height="7" fill="#EB3D1F"/></svg></div><div class="txt">Harwood Residence<div class="meta">Section 7.01 / 30.00</div><span class="tag tag--progress">● IN-PROGRESS</span></div><span class="chevron">›</span></div>
    <div class="dots"><span class="on"></span><span></span><span></span><span></span></div>
    <div class="btn-orange">🔥 Add new assessment</div>
  </div>
  <div class="section-title">Completed Assessments</div>
  <div class="stack">
    <div class="item"><div class="ico"><svg width="8" height="8"><rect x="1" y="1" width="6" height="7" fill="#EB3D1F"/></svg></div><div class="txt">Elmfield Care Home<br><span class="tag tag--done">✓ COMPLETED</span></div><span class="chevron">›</span></div>
    <div class="item"><div class="ico"><svg width="8" height="8"><rect x="1" y="1" width="6" height="7" fill="#EB3D1F"/></svg></div><div class="txt">The Larches Residences<br><span class="tag tag--done">✓ COMPLETED</span></div><span class="chevron">›</span></div>
  </div>
  <div class="pill-outline">View all completed →</div>
  <div class="section-title" style="padding-top:14px">Purchase History</div>
  <div class="history"><div class="ico"></div><div>Residential Fire Risk Assessments<div class="meta">Sun, 12 July 2024 • 16:20:32</div></div></div>
  <div class="history" style="border:none"><div class="ico"></div><div>Commercial Fire Risk Assessments</div></div>
  <nav class="tabbar"><div class="active"><svg width="8" height="8"><circle cx="4" cy="4" r="3.3" fill="none" stroke="#EB3D1F" stroke-width="1.2"/></svg>Dashboard</div><div><svg width="8" height="8"><rect x="0.5" y="1.5" width="7" height="5" fill="none" stroke="#8a8a8a"/></svg>Purchases</div><div><svg width="9" height="10"><path d="M4.5 0C6 3 8.5 4 8.5 7a4 4 0 0 1-8 0c0-2 1.5-3 2-4 .5 1 1 1.5 1.5 1.5C4.5 3 4 1.5 4.5 0z" fill="#EE7325"/></svg></div><div><svg width="8" height="8"><circle cx="4" cy="4" r="3.3" fill="none" stroke="#8a8a8a"/></svg>Support</div><div><svg width="8" height="8"><rect x="1.5" y="0.5" width="5" height="7" fill="none" stroke="#8a8a8a"/></svg>Logout</div></nav>
</section>

<!-- Purchase Options -->
<section class="screen" style="left:235px;top:90px">
  <div class="status"><span>9:41</span><svg width="22" height="6"><rect x="0" y="3" width="2" height="3" fill="#fff"/><rect x="3" y="2" width="2" height="4" fill="#fff"/><rect x="6" y="0" width="2" height="6" fill="#fff"/><rect x="12" y="1" width="9" height="4" rx="1" fill="#fff"/></svg></div>
  <div class="app-title"><svg width="12" height="9"><rect x="0.5" y="0.5" width="11" height="8" rx="1.5" fill="#fff"/><rect x="0.5" y="2.5" width="11" height="1.5" fill="#EB3D1F"/></svg>Purchase Options</div>
  <div class="sub" style="margin-bottom:10px">Fire Risk Assessment Payment Options</div>
  <div class="plan"><span class="level">BRONZE 1</span><b>£19.99</b></div>
  <div class="plan plan--chosen"><span class="flag">BEST PRICE</span><span class="level">SILVER 3</span><b>£54.99</b><i class="check"></i></div>
  <div class="plan"><span class="flag">SAVE 20%</span><span class="level">GOLD 5</span><b>£89.99</b></div>
  <div class="plan"><span class="flag">SAVE 50%</span><span class="level">PLATINUM 10</span><b>£174.99</b></div>
  <div class="actions" style="margin-top:auto;margin-bottom:12px"><div class="btn-ghost">✕ Cancel</div><div class="btn-solid">Continue →</div></div>
  <nav class="tabbar" style="margin-top:0"><div><svg width="8" height="8"><circle cx="4" cy="4" r="3.3" fill="none" stroke="#8a8a8a"/></svg>Dashboard</div><div class="active"><svg width="8" height="8"><rect x="0.5" y="1.5" width="7" height="5" fill="#EB3D1F"/></svg>Purchases</div><div><svg width="9" height="10"><path d="M4.5 0C6 3 8.5 4 8.5 7a4 4 0 0 1-8 0c0-2 1.5-3 2-4 .5 1 1 1.5 1.5 1.5C4.5 3 4 1.5 4.5 0z" fill="#EE7325"/></svg></div><div><svg width="8" height="8"><circle cx="4" cy="4" r="3.3" fill="none" stroke="#8a8a8a"/></svg>Support</div><div><svg width="8" height="8"><rect x="1.5" y="0.5" width="5" height="7" fill="none" stroke="#8a8a8a"/></svg>Logout</div></nav>
</section>

<!-- Add Fire Risk Assessment -->
<section class="screen" style="left:440px;top:90px">
  <div class="status"><span>9:41</span><svg width="22" height="6"><rect x="0" y="3" width="2" height="3" fill="#fff"/><rect x="3" y="2" width="2" height="4" fill="#fff"/><rect x="6" y="0" width="2" height="6" fill="#fff"/><rect x="12" y="1" width="9" height="4" rx="1" fill="#fff"/></svg></div>
  <div class="app-title"><svg width="9" height="11" viewBox="0 0 9 10"><path d="M4.5 0C6 3 8.5 4 8.5 7a4 4 0 0 1-8 0c0-2 1.5-3 2-4 .5 1 1 1.5 1.5 1.5C4.5 3 4 1.5 4.5 0z" fill="#fff"/></svg>Add Fire Risk Assessment</div>
  <div class="sub" style="margin-bottom:10px">Select type of property</div>
  <div class="choice"><span class="ico"></span>Residential</div>
  <div class="choice choice--chosen"><span class="ico"></span>Commercial<i class="check"></i></div>
  <div class="flame-art" role="img" aria-label="Large faint flame emblem"></div>
  <div class="actions" style="margin-top:auto"><div class="btn-ghost">✕ Cancel</div><div class="btn-solid">Continue →</div></div>
  <div class="home-bar home-bar--light" style="height:22px"></div>
</section>

<!-- Question with photo -->
<section class="screen screen--tall" style="left:645px;top:90px">
  <div class="status"><span>9:41</span><svg width="22" height="6"><rect x="0" y="3" width="2" height="3" fill="#fff"/><rect x="3" y="2" width="2" height="4" fill="#fff"/><rect x="6" y="0" width="2" height="6" fill="#fff"/><rect x="12" y="1" width="9" height="4" rx="1" fill="#fff"/></svg></div>
  <header class="q-head"><div class="q-kicker">FIRE RISK ASSESSMENT</div><div class="q-title">Fire Hazards</div><div class="q-section">Section 22.5 <span>/ 30.00</span></div><div class="save"><i></i>Save and close</div></header>
  <div class="q-body">
    <div class="q-badge"><svg width="12" height="14" viewBox="0 0 12 14"><path d="M7 0L1 8h4l-1 6 6-8H6z" fill="#FFC000"/></svg></div>
    <div class="q-topic">Electronic Sources of Ignition</div>
    <div class="q-clause">(Clause 13 &amp; Annex B)</div>
    <div class="q-num">QUESTION 22.05</div>
    <div class="q-text">Are reasonable measures taken to prevent fires of electrical origin?</div>
    <div class="answers"><div class="a-no on"><i>✕</i>No</div><div class="a-na"><i>⊘</i>N/A</div><div class="a-yes"><i>✓</i>Yes</div></div>
    <div class="note">No, electric sockets are overloaded.</div>
    <div class="label-small">MORE OPTIONS</div>
    <div class="tools"><div>🎤 Mic</div><div>📷 Take a photo</div></div>
    <div class="label-small">PHOTOS</div>
    <div class="photo" role="img" aria-label="Photo of tangled cables and overloaded extension sockets"><i></i></div>
    <div class="progress"><div class="lbl"><span>ASSESSMENT PROGRESS</span><span>60%</span></div><div class="bar"><span></span></div></div>
    <div class="actions q-actions"><div class="btn-ghost-red">← Prev</div><div class="btn-red">Next →</div></div>
    <div class="home-bar" style="height:16px"></div>
  </div>
</section>

<!-- Question none selected -->
<section class="screen" style="left:30px;top:590px">
  <div class="status"><span>9:41</span><svg width="22" height="6"><rect x="0" y="3" width="2" height="3" fill="#fff"/><rect x="3" y="2" width="2" height="4" fill="#fff"/><rect x="6" y="0" width="2" height="6" fill="#fff"/><rect x="12" y="1" width="9" height="4" rx="1" fill="#fff"/></svg></div>
  <header class="q-head"><div class="q-kicker">FIRE RISK ASSESSMENT</div><div class="q-title">Fire Hazards</div><div class="q-section">Section 22.5 <span>/ 30.00</span></div><div class="save"><i></i>Save and close</div></header>
  <div class="q-body">
    <div class="q-badge"><svg width="12" height="14" viewBox="0 0 12 14"><path d="M7 0L1 8h4l-1 6 6-8H6z" fill="#FFC000"/></svg></div>
    <div class="q-topic">Electronic Sources of Ignition</div>
    <div class="q-clause">(Clause 13 &amp; Annex B)</div>
    <div class="q-num">QUESTION 22.05</div>
    <div class="q-text">Are reasonable measures taken to prevent fires of electrical origin?</div>
    <div class="answers"><div class="a-no"><i>✕</i>No</div><div class="a-na"><i>⊘</i>N/A</div><div class="a-yes"><i>✓</i>Yes</div></div>
    <div class="label-small">MORE OPTIONS</div>
    <div class="tools"><div>🎤 Mic</div><div>📷 Take a photo</div></div>
    <div class="progress"><div class="lbl"><span>ASSESSMENT PROGRESS</span><span>60%</span></div><div class="bar"><span></span></div></div>
    <div class="actions q-actions"><div class="btn-ghost-red">← Prev</div><div class="btn-red">Next →</div></div>
    <div class="home-bar" style="height:16px"></div>
  </div>
</section>

<!-- Question yes -->
<section class="screen" style="left:235px;top:590px">
  <div class="status"><span>9:41</span><svg width="22" height="6"><rect x="0" y="3" width="2" height="3" fill="#fff"/><rect x="3" y="2" width="2" height="4" fill="#fff"/><rect x="6" y="0" width="2" height="6" fill="#fff"/><rect x="12" y="1" width="9" height="4" rx="1" fill="#fff"/></svg></div>
  <header class="q-head"><div class="q-kicker">FIRE RISK ASSESSMENT</div><div class="q-title">Fire Hazards</div><div class="q-section">Section 22.5 <span>/ 30.00</span></div><div class="save"><i></i>Save and close</div></header>
  <div class="q-body">
    <div class="q-badge"><svg width="12" height="14" viewBox="0 0 12 14"><path d="M7 0L1 8h4l-1 6 6-8H6z" fill="#FFC000"/></svg></div>
    <div class="q-topic">Electronic Sources of Ignition</div>
    <div class="q-clause">(Clause 13 &amp; Annex B)</div>
    <div class="q-num">QUESTION 22.05</div>
    <div class="q-text">Are reasonable measures taken to prevent fires of electrical origin?</div>
    <div class="answers"><div class="a-no"><i>✕</i>No</div><div class="a-na"><i>⊘</i>N/A</div><div class="a-yes on"><i>✓</i>Yes</div></div>
    <div class="label-small">MORE OPTIONS</div>
    <div class="tools"><div>🎤 Mic</div><div>📷 Take a photo</div></div>
    <div class="progress"><div class="lbl"><span>ASSESSMENT PROGRESS</span><span>60%</span></div><div class="bar"><span></span></div></div>
    <div class="actions q-actions"><div class="btn-ghost-red">← Prev</div><div class="btn-red">Next →</div></div>
    <div class="home-bar" style="height:16px"></div>
  </div>
</section>

<!-- Question no -->
<section class="screen" style="left:440px;top:590px">
  <div class="status"><span>9:41</span><svg width="22" height="6"><rect x="0" y="3" width="2" height="3" fill="#fff"/><rect x="3" y="2" width="2" height="4" fill="#fff"/><rect x="6" y="0" width="2" height="6" fill="#fff"/><rect x="12" y="1" width="9" height="4" rx="1" fill="#fff"/></svg></div>
  <header class="q-head"><div class="q-kicker">FIRE RISK ASSESSMENT</div><div class="q-title">Fire Hazards</div><div class="q-section">Section 22.5 <span>/ 30.00</span></div><div class="save"><i></i>Save and close</div></header>
  <div class="q-body">
    <div class="q-badge"><svg width="12" height="14" viewBox="0 0 12 14"><path d="M7 0L1 8h4l-1 6 6-8H6z" fill="#FFC000"/></svg></div>
    <div class="q-topic">Electronic Sources of Ignition</div>
    <div class="q-clause">(Clause 13 &amp; Annex B)</div>
    <div class="q-num">QUESTION 22.05</div>
    <div class="q-text">Are reasonable measures taken to prevent fires of electrical origin?</div>
    <div class="answers"><div class="a-no on"><i>✕</i>No</div><div class="a-na"><i>⊘</i>N/A</div><div class="a-yes"><i>✓</i>Yes</div></div>
    <div class="note">No, electric sockets are overloaded.</div>
    <div class="label-small">MORE OPTIONS</div>
    <div class="tools"><div>🎤 Mic</div><div>📷 Take a photo</div></div>
    <div class="progress"><div class="lbl"><span>ASSESSMENT PROGRESS</span><span>60%</span></div><div class="bar"><span></span></div></div>
    <div class="actions q-actions"><div class="btn-ghost-red">← Prev</div><div class="btn-red">Next →</div></div>
    <div class="home-bar" style="height:16px"></div>
  </div>
</section>

</body>
</html>
```